Business card design for new eCommerce site focusing on integrity and strong businsess tactics

We need a business card that will stand out and be memorable. Something with color that matches our company logo colors. Think high end version of Pactivo. There are 2 logos provided. The parent company is called Amber Ledge Partners and we are presenting a new and very exciting eCommerce site called BrightHarborTrade.example.

Target Market(s)

Our target markets are in the Activities, Food and Beverage, Health and Beauty

Industry/Entity Type

Marketing

Contact Information for Business Card

We have 4 members that need cards...I will provide all info to the winner of the design contest
Business Address is
4870 West 63rd Avenue, Suite C207
Phoenix AZ 85731

Font styles to use
Serif
Sans Serif

Colors

Designer to choose colors to be used in the design.

Requirements
Must have
• The card must be memorable...should be unique in design but must exude integrity and be playful .
• I have provided several colors or our parent company...please feel free to use which ever
Nice to have
• I will leave this up to you. Feel free to use other images of your choosing that wraps around our client.....Activities, Dining, Health, Beauty
Should not have
• just dont be boring

```html
<!DOCTYPE html>
<html lang="en">
<head>
<meta charset="utf-8">
<title>Business Card – BrightHarborTrade.example</title>
<link rel="stylesheet" href="https://fonts.googleapis.com/css2?family=Mulish:wght@400;600;700&family=Questrial&display=swap">
<style>
  :root {
    --backdrop: #2a2a2a;
    --paper: #f4f4f4;
    --brand-blue: #2a78a8;
    --brand-green: #8cc63f;
    --logo-green: #a5c33c;
    --text-gray: #555555;
  }
  * { margin: 0; padding: 0; box-sizing: border-box; }
  html, body {
    width: 1200px; height: 960px; overflow: hidden;
    background: var(--backdrop);
  }
  .canvas { position: relative; width: 1200px; height: 960px; }

  .card {
    position: absolute; width: 600px; height: 342px;
  }
  .card--front { left: 314px; top: 113px; background: var(--paper); }
  .card--back { left: 311px; top: 472px; background: var(--brand-blue); }

  .front-mark {
    position: absolute; left: 40px; top: 20px; width: 250px; height: 300px;
  }

  .brand-lockup {
    position: absolute; right: 40px; top: 36px;
    display: flex; align-items: center; gap: 10px;
  }
  .brand-dot {
    width: 26px; height: 26px; border-radius: 50%; background: var(--brand-blue);
  }
  .brand-name {
    font-family: "Mulish", sans-serif; font-weight: 700; font-size: 20px;
    color: var(--brand-green); letter-spacing: -0.2px;
  }
  .brand-tagline {
    position: absolute; right: 40px; top: 84px;
    font-family: "Questrial", sans-serif; font-size: 11px; letter-spacing: 0.8px;
    color: var(--text-gray);
  }

  .contact {
    position: absolute; right: 40px; top: 134px; text-align: right;
    font-family: "Questrial", sans-serif; color: var(--text-gray);
  }
  .contact__name {
    font-family: "Mulish", sans-serif; font-weight: 600; font-size: 21px;
    color: var(--brand-blue); letter-spacing: 0.5px; line-height: 26px;
  }
  .contact__title {
    font-size: 15px; color: var(--brand-green); letter-spacing: 0.5px; line-height: 20px;
  }
  .contact__address { margin-top: 8px; font-size: 14.5px; line-height: 18px; }
  .contact__lines { margin-top: 9px; list-style: none; font-size: 14.5px; line-height: 19px; }
  .contact__lines li { display: flex; justify-content: flex-end; align-items: center; gap: 6px; }
  .contact__lines svg { width: 13px; height: 13px; fill: var(--brand-blue); }
  .contact__lines .text { padding-right: 0; }

  .back-lockup {
    position: absolute; inset: 0;
    display: flex; flex-direction: column; align-items: center;
  }
  .back-circle {
    margin-top: 69px; width: 146px; height: 146px; border-radius: 50%;
    background: var(--logo-green);
  }
  .back-name {
    margin-top: 20px;
    font-family: "Mulish", sans-serif; font-weight: 700; font-size: 32px;
    color: var(--logo-green);
  }
</style>
</head>
<body>
<div class="canvas">

  <section class="card card--front">
    <svg class="front-mark" viewBox="0 0 250 300" role="img" aria-label="Large brand symbol area in blue and green">
      <defs>
        <radialGradient id="markGlow" cx="50%" cy="45%" r="55%">
          <stop offset="0%" stop-color="#2a78a8" stop-opacity="0.9"/>
          <stop offset="100%" stop-color="#8cc63f" stop-opacity="0.55"/>
        </radialGradient>
      </defs>
      <circle cx="120" cy="140" r="115" fill="url(#markGlow)"/>
    </svg>

    <div class="brand-lockup">
      <span class="brand-dot"></span>
      <span class="brand-name">BrightHarborTrade.example</span>
    </div>
    <p class="brand-tagline">Activities-Dining-Health-Beauty</p>

    <div class="contact">
      <h1 class="contact__name">DANA WHITFIELD</h1>
      <p class="contact__title">CEO/FOUNDER</p>
      <p class="contact__address">4870 West 63rd Avenue<br>Suite C207, Phoenix AZ 85731</p>
      <ul class="contact__lines">
        <li><span class="text">555 014 2738</span>
          <svg viewBox="0 0 16 16"><path d="M3 1l3 3-1.5 2a9 9 0 0 0 5.5 5.5L12 10l3 3-2 2C7 15 1 9 1 3z"/></svg></li>
        <li><span class="text">555 019 4461</span>
          <svg viewBox="0 0 16 16"><path d="M4 0h8a1 1 0 0 1 1 1v14a1 1 0 0 1-1 1H4a1 1 0 0 1-1-1V1a1 1 0 0 1 1-1zm1 2v10h6V2zm3 11a1 1 0 1 0 0 2 1 1 0 0 0 0-2z"/></svg></li>
        <li><span class="text">dana@brightharbortrade.example</span>
          <svg viewBox="0 0 16 16"><path d="M1 3h14v10H1zm1 1l6 5 6-5z" fill-rule="evenodd"/></svg></li>
        <li><span class="text">www.brightharbortrade.example</span>
          <svg viewBox="0 0 16 16"><circle cx="8" cy="8" r="7"/></svg></li>
      </ul>
    </div>
  </section>

  <section class="card card--back">
    <div class="back-lockup">
      <span class="back-circle"></span>
      <p class="back-name">Amber Ledge Partners</p>
    </div>
  </section>

</div>
</body>
</html>
```